Tampa Bay fishing guide needs stunning website.

I currently have a site - www.reelcoveguide.net which I personally put together using the Pagely platform and I am looking for a redesign on a different platform (Sitecraft?) that will allow me to easily create landing pages in the future. Would like to have a block for visitors to opt in to newsletter. Need social media links on all pages.

I would like to let my visitors know that I am able to handle their fishing charter needs here in the Tampa Bay area, if I'm not available for the dates they are looking to go I can refer them to a reputable captain in the area.

Target Market(s)

United States

Industry/Entity Type

Tourism

Coding

Coded - Design and coding required

Number of Pages Required

5+ page

Font styles to use
Sans Serif

Colors
0355a3
3176b5
85abd2
fbf289

Requirements
Must have
• Mobile Responsive, Ability to insert Vantor Metrics, Chatterbox pixels, ability to add custom landing pages in future
Nice to have
• Clean, easy navigation

```html
<!DOCTYPE html>
<html lang="en">
<head>
<meta charset="utf-8">
<title>Halvorsen Tampa Bay Fishing Charters</title>
<link href="https://fonts.googleapis.com/css2?family=Oswald:wght@400;500;600&family=Open+Sans:wght@400;600;700&family=Merriweather:ital@1&display=swap" rel="stylesheet">
<style>
:root{
  --blue-deep:#0355a3;
  --blue-mid:#3176b5;
  --blue-light:#85abd2;
  --yellow:#fbf289;
  --yellow-strong:#f3dd3c;
  --ink:#1c1c1c;
  --text:#6b6b6b;
  --navy:#0a3f86;
  --grey-band:#ececec;
  --dark-band:#3a3a3a;
  --white:#ffffff;
}
*{box-sizing:border-box;margin:0;padding:0}
html,body{width:1200px;height:2965px;overflow:hidden}
body{font-family:"Open Sans",Arial,sans-serif;color:var(--text);background:var(--white);position:relative}
.abs{position:absolute}
.head{font-family:"Oswald",Arial,sans-serif;text-transform:uppercase;color:var(--ink);font-weight:500}
.head .accent{color:var(--blue-deep)}

/* header */
.site-header{left:0;top:0;width:1200px;height:103px;background:var(--white)}
.brand{left:99px;top:26px;display:flex;align-items:center;gap:12px;font-family:"Oswald",sans-serif;font-size:34px;font-weight:500;color:var(--blue-deep)}
.brand .dot{width:16px;height:16px;border-radius:50%;background:var(--blue-mid)}
.social{right:99px;top:31px;display:flex;gap:12px}
.social span{width:40px;height:40px;border-radius:50%;display:block;background:var(--blue-mid)}

/* nav */
.main-nav{left:0;top:103px;width:1200px;height:59px;background:linear-gradient(var(--blue-mid),var(--blue-deep))}
.main-nav ul{list-style:none;display:flex;position:absolute;left:99px;top:0;height:59px}
.main-nav li{font-size:13px;color:var(--white);line-height:59px;padding:0 28px;text-transform:uppercase}
.main-nav li.active{background:var(--blue-deep)}
.nav-phone{right:99px;top:13px;font-family:"Oswald",sans-serif;color:var(--white);font-size:18px}
.nav-phone b{font-size:25px;font-weight:500}

/* hero */
.hero{left:0;top:162px;width:1200px;height:534px;background:linear-gradient(180deg,#4f6a70 0%,#6f8c8c 45%,#2f4d5a 100%)}
.hero-title{width:1200px;top:150px;text-align:center;font-family:"Oswald",sans-serif;color:var(--white);font-size:50px;font-weight:500;text-transform:uppercase}
.hero-sub{width:1200px;top:222px;text-align:center;font-family:"Oswald",sans-serif;color:var(--white);font-size:34px}
.search{left:176px;top:322px;display:flex;gap:12px}
.field{height:42px;border:1px solid rgba(255,255,255,.8);background:rgba(0,0,0,.35);color:var(--white);font-size:13px;padding:0 18px;line-height:40px;width:226px;display:flex;justify-content:space-between}
.btn-search{width:142px;height:42px;background:linear-gradient(var(--yellow),var(--yellow-strong));color:var(--ink);font-weight:700;font-size:14px;line-height:42px;text-align:center;text-transform:uppercase}
.dots{left:557px;top:476px;display:flex;gap:6px}
.dots span{width:13px;height:13px;border:2px solid var(--white);border-radius:50%}

/* welcome */
.welcome-title{left:99px;top:736px;font-size:33px}
.welcome-sub{left:99px;top:788px;font-size:20px;color:#333}
.welcome-copy{left:99px;top:836px;width:500px;font-size:11.5px;line-height:21px}
.welcome-copy p{margin-bottom:17px}
.video{left:633px;top:761px;width:468px;height:271px;border:6px solid var(--white);box-shadow:0 0 8px rgba(0,0,0,.3);background:linear-gradient(135deg,#2d6b6a,#c7c2b5 60%,#e6e2d8)}
.play{left:199px;top:99px;width:58px;height:58px;border-radius:50%;background:rgba(0,0,0,.45);border:2px solid var(--white)}

/* services band */
.services{left:0;top:1101px;width:1200px;height:372px;background:linear-gradient(var(--blue-deep),var(--blue-mid) 50%,var(--blue-deep))}
.services-title{width:1200px;top:42px;text-align:center;font-family:"Oswald",sans-serif;font-size:33px;color:var(--white);text-transform:uppercase}
.services-title span{color:var(--yellow)}
.services-sub{width:1200px;top:94px;text-align:center;font-family:"Merriweather",serif;font-style:italic;color:var(--white);font-size:13px}
.card{top:152px;width:314px;height:168px;border:2px solid var(--yellow);text-align:center;color:var(--white);padding:20px 22px}
.card h3{font-family:"Oswald",sans-serif;font-weight:400;color:var(--yellow);font-size:20px;text-transform:uppercase;margin-bottom:8px}
.card p{font-size:11.5px;line-height:22px}
.card a{display:block;margin-top:8px;color:var(--yellow);font-weight:700;font-size:13px}

/* day charters */
.feature-title{top:1514px;font-size:25px}
.photo{border:6px solid var(--white);box-shadow:0 0 8px rgba(0,0,0,.25)}
.feature-copy{top:1818px;width:468px;font-size:11.5px;line-height:24px}
.read-more{top:1876px;color:var(--blue-deep);font-weight:700;font-size:13px;text-transform:uppercase}

/* blog */
.blog{left:0;top:1937px;width:1200px;height:499px;background:var(--grey-band)}
.blog-title{width:1200px;top:36px;text-align:center;font-size:33px}
.post{top:109px;width:318px}
.post .photo{height:192px}
.post h4{font-family:"Oswald",sans-serif;font-weight:500;color:var(--ink);font-size:15px;margin-top:16px;text-transform:uppercase}
.post .meta{font-size:11px;margin-top:8px;display:flex;gap:22px}
.post p{font-size:11.5px;line-height:22px;margin-top:12px}

/* newsletter */
.newsletter{left:0;top:2436px;width:1200px;height:118px;background:var(--dark-band)}
.mail-badge{left:99px;top:22px;width:76px;height:76px;border-radius:50%;background:var(--white);border:6px solid var(--blue-deep)}
.news-title{left:203px;top:20px;font-family:"Oswald",sans-serif;color:var(--white);font-size:22px;text-transform:uppercase}
.news-copy{left:203px;top:56px;width:420px;color:#ddd;font-size:11.5px;line-height:22px}
.news-input{left:630px;top:38px;width:328px;height:44px;background:var(--white);border:1px solid #ccc;font-size:11px;color:#999;padding:0 14px;line-height:42px}
.news-btn{left:972px;top:38px;width:130px;height:44px;background:linear-gradient(var(--yellow),var(--yellow-strong));color:var(--ink);font-weight:700;font-size:14px;line-height:44px;text-align:center;text-transform:uppercase}

/* footer */
.footer{left:0;top:2554px;width:1200px;height:348px;background:linear-gradient(var(--blue-deep),var(--navy))}
.foot-brand{left:99px;top:30px;font-family:"Oswald",sans-serif;color:var(--white);font-size:34px;font-weight:500;display:flex;gap:12px;align-items:center}
.foot-brand .dot{width:16px;height:16px;border-radius:50%;background:var(--blue-light)}
.contact{left:99px;top:128px;list-style:none;color:var(--white);font-size:11.5px}
.contact li{display:flex;align-items:center;gap:14px;height:30px}
.contact svg{width:12px;height:12px;fill:var(--white)}
.foot-social{left:99px;top:272px;display:flex;gap:9px}
.foot-social span{width:24px;height:24px;border:1px solid var(--blue-light);border-radius:50%}
.foot-col{top:54px;color:var(--white)}
.foot-col h5{font-family:"Oswald",sans-serif;font-weight:400;font-size:17px;text-transform:uppercase;margin-bottom:18px}
.foot-col ul{list-style:none;font-size:11px;line-height:30px;text-transform:uppercase}
.copyright{left:0;top:2902px;width:1200px;height:63px;background:#062f66;color:var(--white);font-size:12px;text-align:center;line-height:63px}
</style>
</head>
<body>

<header class="abs site-header">
  <div class="abs brand"><span class="dot"></span>Halvorsen</div>
  <div class="abs social" aria-label="Social links">
    <span></span><span></span><span></span><span></span><span></span><span></span>
  </div>
</header>

<nav class="abs main-nav">
  <ul>
    <li class="active">Home</li><li>About Us</li><li>Pick Up Locations</li><li>Rates</li><li>Contact Us</li>
  </ul>
  <div class="abs nav-phone">Call Capt. Rory <b>(555) 014-2290</b></div>
</nav>

<section class="abs hero" role="img" aria-label="Anglers on a boat fighting a leaping tarpon on Tampa Bay">
  <h1 class="abs hero-title">We Are Tampa Bay Fishing Charters</h1>
  <p class="abs hero-sub">Take Action Towards Your Dream</p>
  <div class="abs search">
    <div class="field">Where to <span>▾</span></div>
    <div class="field">Check in <span>▦</span></div>
    <div class="field">Check out <span>▦</span></div>
    <div class="btn-search">Search Now</div>
  </div>
  <div class="abs dots"><span></span><span></span><span></span><span></span><span></span></div>
</section>

<h2 class="abs head welcome-title">Welcome to <span class="accent">Halvorsen</span></h2>
<p class="abs welcome-sub">Tampabay,fishingguide,tampabay fishing Charters</p>
<div class="abs welcome-copy">
  <p>Capt. Rory Halvorsen, with over 20 years' experience, Native fishing charter tampa charter captain offering full and half day fishing charters on the waters of Tampa Bay.</p>
  <p>If you're looking for a great fishing charter tampa don't hesitate to contact Capt. Rory or you can simply book your trip online here.</p>
  <p>Come enjoy a wonderful day fishing charters Tampa for Tarpon, Snook, Redfish, Trout, Sharks, Cobia, Spanish mackerel as well as others aboard Capt. Rory Halvorsen Sport fishing Charters boat. Capt. Rory will work hard to ensure that you and your guests have a memorable day enjoying the wonderful gamefish that Tampa Bay has to offer.</p>
</div>
<div class="abs video" role="img" aria-label="Video still of anglers landing a tarpon beside the boat">
  <div class="abs play"><svg width="54" height="54" viewBox="0 0 54 54"><polygon points="21,16 38,27 21,38" fill="#fff"/></svg></div>
</div>

<section class="abs services">
  <h2 class="abs services-title">Tampa Bay <span>Fishing Charters Florida</span></h2>
  <p class="abs services-sub">Come enjoy a wonderful day fishing charters Tampa for Tarpon, Snook, Redfish, Trout, Sharks Cobia, Spanish mackerel</p>
  <div class="abs card" style="left:99px"><h3>Fishing Charters</h3><p>Rory Halvorsen Sport fishing Charters boat. Capt. Rory will work hard to ensure that you and your guests have a memorable day enjoying</p><a>Read More</a></div>
  <div class="abs card" style="left:443px"><h3>Rates &amp; Information</h3><p>Rory Halvorsen Sport fishing Charters boat. Capt. Rory will work hard to ensure that you and your guests have a memorable day enjoying</p><a>Read More</a></div>
  <div class="abs card" style="left:787px"><h3>Charter Trips</h3><p>Rory Halvorsen Sport fishing Charters boat. Capt. Rory will work hard to ensure that you and your guests have a memorable day enjoying</p><a>Read More</a></div>
</section>

<h2 class="abs head feature-title" style="left:99px">Full &amp; Half <span class="accent">Day Charters</span></h2>
<div class="abs photo" style="left:99px;top:1568px;width:466px;height:227px;background:linear-gradient(#1d4f8a,#2f6aa8 60%,#1b3f70)" role="img" aria-label="Angler on the water holding up a snook"></div>
<p class="abs feature-copy" style="left:99px">Offering Tampa Bay, FL fishing charters on the beautiful waters of Tampa Bay. Fish with Capt. Rory Halvorsen, Tampa Bay, FL fishing guide for over 20 years</p>
<span class="abs read-more" style="left:99px">Read More</span>

<h2 class="abs head feature-title" style="left:633px">Multiple <span class="accent">Pickup Points</span></h2>
<div class="abs photo" style="left:633px;top:1568px;width:468px;height:227px;background:linear-gradient(160deg,#3fb4a8,#1f8f8a 60%,#156b70)" role="img" aria-label="School of tarpon swimming in clear green water"></div>
<p class="abs feature-copy" style="left:633px">Offering Tampa Bay, FL fishing charters on the beautiful waters of Tampa Bay. Fish with Capt. Rory Halvorsen, Tampa Bay, FL fishing guide for over 20 years</p>
<span class="abs read-more" style="left:633px">Read More</span>

<section class="abs blog">
  <h2 class="abs head blog-title">Our Latest <span class="accent">Blog Post</span></h2>
  <article class="abs post" style="left:99px">
    <div class="photo" style="background:linear-gradient(135deg,#2f5a2a,#6f8f4e)" role="img" aria-label="Angler holding a large snook among mangroves"></div>
    <h4>Half Day (4 Hour) Charter 1-3 People</h4>
    <div class="meta"><span>◷ July 04,2016</span><span>▰ 15 Comments</span></div>
    <p>Enjoy a half day trip on the beautiful waters of Tampa Bay. Trip includes all bait, tackle and licenses. Just bring your food and drinks (cooler provided onboard).</p>
  </article>
  <article class="abs post" style="left:441px">
    <div class="photo" style="background:linear-gradient(#cfcfc8,#9fa6a0)" role="img" aria-label="Two anglers casting from a boat on a hazy morning"></div>
    <h4>3/4 Day (6 Hour) Charter 1-3 People</h4>
    <div class="meta"><span>◷ July 04,2016</span><span>▰ 15 Comments</span></div>
    <p>Our most popular and recommended trip. Enjoy a 6 hour trip on the beautiful waters of Tampa Bay. Trip includes all bait, tackle and licenses.</p>
  </article>
  <article class="abs post" style="left:783px">
    <div class="photo" style="background:linear-gradient(#7a8f7a,#3a6aa8 55%,#c7c0a8)" role="img" aria-label="Angler in a blue shirt holding a snook"></div>
    <h4>Full Day (8 Hours) Charter 1-3 People</h4>
    <div class="meta"><span>◷ July 04,2016</span><span>▰ 15 Comments</span></div>
    <p>Enjoy a full day trip on the beautiful waters of Tampa Bay. Trip includes all bait, tackle and licenses. Just bring your food and drinks (cooler provided onboard).</p>
  </article>
</section>

<section class="abs newsletter">
  <div class="abs mail-badge"><svg width="64" height="64" viewBox="0 0 64 64"><rect x="20" y="24" width="24" height="17" fill="#0355a3"/><polyline points="20,24 32,34 44,24" fill="none" stroke="#fff" stroke-width="2"/></svg></div>
  <h3 class="abs news-title">Signup for Newsletter</h3>
  <p class="abs news-copy">I must explain to you how all this mistaken idea of denouncing pleasure and praising pain was born and I will complete account</p>
  <div class="abs news-input">Enter Mail ID</div>
  <div class="abs news-btn">Signup Now</div>
</section>

<footer class="abs footer">
  <div class="abs foot-brand"><span class="dot"></span>Halvorsen</div>
  <ul class="abs contact">
    <li><svg viewBox="0 0 12 12"><path d="M6 0a4 4 0 0 1 4 4c0 3-4 8-4 8S2 7 2 4a4 4 0 0 1 4-4z"/></svg>48 Harborline Way &nbsp;&nbsp;&nbsp;Suite 12-B</li>
    <li><svg viewBox="0 0 12 12"><path d="M2 0h3l1 3-2 1a7 7 0 0 0 4 4l1-2 3 1v3c0 1-1 2-2 2C5 12 0 7 0 2 0 1 1 0 2 0z"/></svg>Phone - 1800 555 0147</li>
    <li><svg viewBox="0 0 12 12"><rect x="1" y="4" width="10" height="6"/><rect x="3" y="1" width="6" height="3"/></svg>Fax - 03 555 0192</li>
    <li><svg viewBox="0 0 12 12"><rect x="0" y="2" width="12" height="8"/></svg>E-mail - support@halvorsencharters.com</li>
  </ul>
  <div class="abs foot-social"><span></span><span></span><span></span><span></span><span></span><span></span></div>
  <div class="abs foot-col" style="left:440px"><h5>About Halvorsen</h5><ul><li>Who we are</li><li>Company History</li><li>Travel</li><li>Partners</li><li>Privacy Notice</li></ul></div>
  <div class="abs foot-col" style="left:684px"><h5>Customer Service</h5><ul><li>Adventure</li><li>Feedback</li><li>Contact Us</li><li>Capt Advisories</li><li>FAQ</li><li>Site Map</li></ul></div>
  <div class="abs foot-col" style="left:940px"><h5>Others</h5><ul><li>Blog</li><li>News&amp;Medias</li><li>Capt. Guide</li></ul></div>
</footer>

<div class="abs copyright">Copyrights@2016Company Name , All rights reserved</div>

</body>
</html>
```